Webdesign für Steuerberaterin
Zielgruppe
Ich bin Steuerberaterin. Meine Zielgruppe sind sowohl Privatpersonen als auch Unternehmer sowie Männer und Frauen.
Aufgabenstellung
Bitte mein Logo und Foto mit berücksichtigen. Ich möchte keine Website, auf der alle 'Reiter' als eine Seite von oben nach unten durchlaufen. Sondern wirklich einzelne, voneinander getrennte Seiten.

```html
<!DOCTYPE html>
<html lang="de">
<head>
<meta charset="utf-8">
<title>Maren Brodtke Steuerberaterin – Webdesign</title>
<link href="https://fonts.googleapis.com/css2?family=EB+Garamond:wght@400&family=Montserrat:wght@400;500&display=swap" rel="stylesheet">
<style>
:root{
  --stage:#f4f2ee;
  --paper:#ffffff;
  --mist:#f4f4f4;
  --gold:#d5a223;
  --ink:#2b2a2c;
  --line:#e6e6e6;
  --photo-light:#e9e8e6;
  --photo-dark:#1b1e29;
}
*{margin:0;padding:0;box-sizing:border-box}
html,body{width:1200px;height:987px;overflow:hidden;background:var(--stage)}
body{position:relative;font-family:"Montserrat",sans-serif;color:var(--ink)}
.serif{font-family:"EB Garamond",serif;font-weight:400}
.abs{position:absolute}

/* desktop screen */
.desktop{position:absolute;left:68px;top:52px;width:922px;height:799px;background:var(--paper);box-shadow:0 8px 30px rgba(0,0,0,.08);overflow:hidden}
.desktop .mist{left:553px;top:0;width:369px;height:379px;background:var(--mist)}
.brand{display:flex;align-items:center;gap:4px;color:var(--ink);font-family:"EB Garamond",serif;line-height:1.05}
.brand .dot{width:7px;height:7px;border-radius:50%;background:var(--gold);flex:none}
.nav{top:10px;left:669px;display:flex;gap:0;font-size:6px;letter-spacing:.02em}
.nav a{color:var(--ink);text-decoration:none;height:15px;display:flex;align-items:center}
.nav .active{color:var(--gold);border:1px solid var(--gold);padding:0 8px}
.photo-desk{left:492px;top:64px;width:257px;height:336px;background:linear-gradient(180deg,#eeedeb 0%,#e2e1df 45%,#2a2d3a 75%,#1c1f2a 100%)}
.hero-title{left:163px;top:167px;font-size:26px;line-height:1;}
.hero-sub{left:163px;top:223px;font-size:7px}
.btn{position:absolute;height:26px;display:flex;align-items:center;justify-content:space-between;padding:0 10px;font-size:6px;letter-spacing:.02em}
.btn svg{width:5px;height:6px}
.btn-outline{border:1px solid var(--ink);color:var(--ink)}
.btn-gold{background:var(--gold);color:#fff}
.band{left:97px;top:450px;width:825px;height:221px;background:var(--gold);color:#fff}
.band-line{left:264px;top:432px;width:1px;height:36px;background:var(--ink)}
.band-title{font-size:15px;line-height:1}
.band-copy{font-size:5.4px;line-height:1.32}
.band-copy p+p{margin-top:7px}
.divider{left:0;top:695px;width:922px;height:1px;background:var(--line)}
.copy{font-size:5.8px}
.foot-head{font-size:6.5px;margin-bottom:3px}
.foot-col a{display:block;font-size:5.8px;color:var(--ink);text-decoration:none;line-height:11px}

/* mobile screen */
.mobile{position:absolute;left:952px;top:113px;width:180px;height:810px;background:var(--paper);box-shadow:0 8px 30px rgba(0,0,0,.1);overflow:hidden}
.photo-mob{left:0;top:60px;width:180px;height:331px;background:linear-gradient(180deg,#ecebe9 0%,#dcdcdc 30%,#565a66 55%,#1b1e29 75%,#151823 100%)}
.burger{left:158px;top:25px;width:12px}
.burger span{display:block;height:1px;background:var(--ink);margin-bottom:3px}
.burger span:last-child{width:8px;margin-left:4px}
</style>
</head>
<body>

<section class="desktop" aria-label="Startseite Desktop">
  <div class="abs mist"></div>
  <div class="abs brand" style="left:67px;top:42px;font-size:12px;flex-direction:column;align-items:flex-start;gap:2px">
    <span style="display:flex;align-items:center;gap:4px"><span class="dot"></span>Maren Brodtke</span>
    <span style="font-size:5px;letter-spacing:.15em;font-family:'EB Garamond',serif">STEUERBERATERIN</span>
  </div>
  <nav class="abs nav">
    <a class="active">START</a>
    <a style="margin-left:21px">ÜBER MICH</a>
    <a style="margin-left:29px">LEISTUNGEN</a>
    <a style="margin-left:29px">KONTAKT</a>
  </nav>

  <div class="abs photo-desk" role="img" aria-label="Porträtfoto der Steuerberaterin vor heller Steinwand"></div>

  <h1 class="abs hero-title serif">Schön,<br>dass Sie da sind!</h1>
  <p class="abs hero-sub">Ich freue mich, dass Sie den Weg zu mir gefunden haben!</p>
  <a class="btn btn-outline" style="left:163px;top:268px;width:96px">ÜBER MICH <svg viewBox="0 0 5 8"><path d="M1 1l3 3-3 3" fill="none" stroke="currentColor"/></svg></a>
  <a class="btn btn-gold" style="left:269px;top:268px;width:96px">LEISTUNGEN <svg viewBox="0 0 5 8"><path d="M1 1l3 3-3 3" fill="none" stroke="currentColor"/></svg></a>

  <div class="abs band">
    <h2 class="abs band-title serif" style="left:66px;top:61px">Sie sind bei mir<br>genau richtig.</h2>
    <div class="abs band-copy" style="left:186px;top:62px;width:218px">
      <p>Egal, ob Sie Privatperson sind, die Ihre Einkommensteuer-Erklärung in vertrauensvolle Hände geben möchte, oder Unternehmer, der sich z.B. das „Rundum-Sorglos-Paket“ mit Buchführung, Jahresabschluss und Steuererklärungen wünscht.</p>
      <p>Schauen Sie sich hier gerne um und melden Sie sich bei mir – ich bin bei jedem steuerlichen Thema gerne Ihr kompetenter und zuverlässiger Ansprechpartner.</p>
      <p>Für mich ist es eine Selbstverständlichkeit, dass ich auch nach mehr als 12 Jahren Berufserfahrung durch permanente Fortbildungen immer auf dem aktuellsten Stand der relevanten Gesetze und Verordnungen bin. Nur so kann ich Sie bestmöglich beraten.</p>
    </div>
  </div>
  <div class="abs band-line"></div>

  <div class="abs divider"></div>
  <div class="abs brand" style="left:163px;top:735px;font-size:9px"><span class="dot" style="width:5px;height:5px"></span>Maren Brodtke</div>
  <p class="abs copy" style="left:163px;top:768px">© 2021 — Maren Brodtke Steuerberaterin</p>
  <div class="abs foot-col" style="left:612px;top:718px">
    <p class="foot-head serif">Navigation</p>
    <a>Start</a><a>Über mich</a><a>Leistungen</a><a>Kontakt</a>
  </div>
  <div class="abs foot-col" style="left:693px;top:718px">
    <p class="foot-head serif">Rechtliches</p>
    <a>Datenschutzerklärung</a><a>AGB</a><a>Impressum</a>
  </div>
</section>

<section class="mobile" aria-label="Startseite Mobil">
  <div class="abs brand" style="left:10px;top:22px;font-size:8px"><span class="dot" style="width:4px;height:4px"></span>Maren Brodtke</div>
  <div class="abs burger"><span></span><span></span></div>

  <div class="abs photo-mob" role="img" aria-label="Porträtfoto der Steuerberaterin, unten dunkel verlaufend"></div>
  <h1 class="abs serif" style="left:11px;top:218px;font-size:19px;line-height:1;color:#fff">Schön,<br>dass sie da sind!</h1>
  <p class="abs" style="left:11px;top:261px;font-size:5.6px;line-height:1.3;color:#fff;width:100px">Ich freue mich, dass Sie den Weg zu mir gefunden haben!</p>
  <a class="btn" style="left:11px;top:296px;width:77px;border:1px solid #fff;color:#fff">ÜBER MICH <svg viewBox="0 0 5 8"><path d="M1 1l3 3-3 3" fill="none" stroke="currentColor"/></svg></a>
  <a class="btn btn-gold" style="left:93px;top:296px;width:77px">LEISTUNGEN <svg viewBox="0 0 5 8"><path d="M1 1l3 3-3 3" fill="none" stroke="currentColor"/></svg></a>

  <div class="abs" style="left:11px;top:349px;width:169px;height:250px;background:var(--gold);color:#fff">
    <h2 class="abs band-title serif" style="left:10px;top:34px;font-size:14px">Sie sind bei mir<br>genau richtig.</h2>
    <div class="abs band-copy" style="left:10px;top:80px;width:143px">
      <p>Egal, ob Sie Privatperson sind, die Ihre Einkommensteuer-Erklärung in vertrauensvolle Hände geben möchte, oder Unternehmer, der sich z.B. das „Rundum-Sorglos-Paket“ mit Buchführung, Jahresabschluss und Steuererklärungen wünscht.</p>
      <p>Schauen Sie sich hier gerne um und melden Sie sich bei mir – ich bin bei jedem steuerlichen Thema gerne Ihr kompetenter und zuverlässiger Ansprechpartner.</p>
      <p>Für mich ist es eine Selbstverständlichkeit, dass ich auch nach mehr als 12 Jahren Berufserfahrung durch permanente Fortbildungen immer auf dem aktuellsten Stand der relevanten Gesetze und Verordnungen bin. Nur so kann ich Sie bestmöglich beraten.</p>
    </div>
  </div>

  <div class="abs" style="left:0;top:622px;width:180px;height:1px;background:var(--line)"></div>
  <div class="abs brand" style="left:11px;top:660px;font-size:8px"><span class="dot" style="width:4px;height:4px"></span>Maren Brodtke</div>
  <p class="abs copy" style="left:11px;top:690px">© 2021 — Maren Brodtke Steuerberaterin</p>
  <div class="abs foot-col" style="left:11px;top:712px">
    <p class="foot-head serif">Navigation</p>
    <a>Start</a><a>Über mich</a><a>Leistungen</a><a>Kontakt</a>
  </div>
  <div class="abs foot-col" style="left:91px;top:712px">
    <p class="foot-head serif">Rechtliches</p>
    <a>Datenschutzerklärung</a><a>AGB</a><a>Impressum</a>
  </div>
</section>

</body>
</html>
```